Website for Torvel Capital - investment banking firm

We have a corporate identity (thanks to Ravinka/31842) and want to extend that into a website design.  See the attached zipped files.
We have software folks in-house to do the coding.
See the attached Project Brief & Notes for more details.  Don't worry about the actual text - lorem ipsum will be fine.
The server will be Apache.
Thank you!
Desmond

Industry/Entity Type
Investment

```html
<!DOCTYPE html>
<html lang="en">
<head>
<meta charset="utf-8">
<title>Torvel Capital</title>
<link rel="stylesheet" href="https://fonts.googleapis.com/css2?family=Cinzel:wght@400;700&family=Open+Sans:wght@400;600;700&family=Merriweather:wght@400;700&display=swap">
<style>
:root{
  --blue:#2a97c4;
  --blue-dark:#1b7eb0;
  --navy:#1c2a3a;
  --ink:#333a42;
  --muted:#6d7379;
  --line:#d9dde0;
  --footer:#1f2328;
  --white:#ffffff;
}
*{box-sizing:border-box;margin:0;padding:0}
html,body{width:1200px;height:2248px;overflow:hidden;background:var(--white);font-family:"Open Sans",Arial,sans-serif;color:var(--ink)}
.page{position:relative;width:1200px;height:2248px}

.site-header{position:absolute;top:0;left:0;width:1200px;height:56px;background:var(--white);z-index:2}
.brand{position:absolute;left:96px;top:12px;display:flex;align-items:center;gap:10px}
.brand-mark{width:30px;height:30px;background:var(--navy)}
.brand-name{font-family:"Cinzel",serif;font-size:22px;font-weight:400;color:var(--navy);letter-spacing:1px}
.util{position:absolute;right:96px;top:0;height:18px;background:var(--navy);color:#fff;font-size:10px;padding:3px 12px;letter-spacing:.5px}
.main-nav{position:absolute;right:96px;top:26px;display:flex;gap:0;font-size:11px;font-weight:600;color:var(--ink)}
.main-nav span{padding:0 12px;border-left:1px solid var(--line)}
.main-nav span:first-child{border-left:none}

.hero{position:absolute;top:56px;left:0;width:1200px;height:524px;background:linear-gradient(180deg,#8a7c7a 0%,#c9a892 35%,#9f8a86 55%,#4f5a6c 80%,#2f3947 100%)}
.hero-title{position:absolute;top:222px;width:100%;text-align:center;font-family:"Cinzel",serif;color:#fff;font-size:40px;letter-spacing:2px}
.hero-title small{font-size:28px}
.hero-sub{position:absolute;top:280px;width:100%;text-align:center;color:#fff;font-size:24px;line-height:34px}
.cta{position:absolute;top:556px;left:465px;width:270px;height:52px;border-radius:26px;background:var(--blue);color:#fff;font-size:16px;font-weight:600;display:flex;align-items:center;justify-content:center;gap:14px;z-index:2}

.intro{position:absolute;top:660px;left:210px;width:780px;text-align:center;font-size:15px;line-height:26px;color:var(--muted)}
.intro b{font-family:"Cinzel",serif;font-size:34px;color:var(--navy);font-weight:400}
.rule{position:absolute;top:800px;left:140px;width:920px;height:1px;background:var(--line)}

.services{position:absolute;top:836px;left:120px;width:960px;display:flex;justify-content:space-between}
.service{width:210px;text-align:center}
.service svg{height:60px}
.service h3{margin-top:30px;font-size:15px;font-weight:700;color:var(--ink)}
.service p{margin-top:14px;font-size:13px;line-height:24px;color:var(--muted);text-align:left;padding:0 8px}
.service a{display:block;margin-top:50px;font-size:13px;font-weight:700;color:var(--blue-dark);text-decoration:none}

.testimonials{position:absolute;top:1224px;left:0;width:1200px;height:396px;background:var(--blue)}
.testimonials h2{position:absolute;left:120px;top:36px;color:#fff;font-size:26px;font-weight:600}
.quotes{position:absolute;top:100px;left:120px;width:960px;display:flex;justify-content:space-between}
.quote{width:306px;text-align:center}
.quote p{background:#fff;color:var(--muted);font-size:11px;line-height:18px;padding:14px 20px;text-align:left;height:104px}
.avatar{width:64px;height:64px;border-radius:50%;margin:38px auto 0;background:linear-gradient(135deg,#c69a7c,#5a4337);border:2px solid #fff}
.quote .who{margin-top:10px;color:#fff;font-size:12px;line-height:17px}

.news{position:absolute;top:1676px;left:120px;width:960px}
.news h2{font-size:26px;font-weight:700;color:var(--ink)}
.news-list{display:flex;justify-content:space-between;margin-top:36px}
.news-item{width:290px}
.news-item h3{font-size:19px;line-height:28px;color:var(--blue-dark);font-weight:700}
.news-item p{margin-top:14px;font-size:13px;line-height:24px;color:var(--muted)}
.news-item time{display:block;margin-top:22px;font-size:12px;color:var(--muted)}
.more{position:absolute;top:2100px;width:100%;text-align:center;font-size:15px;font-weight:700;color:var(--blue-dark)}

.site-footer{position:absolute;top:2180px;left:0;width:1200px;height:68px;background:var(--footer);color:#b7bcc2;font-size:12px}
.foot-brand{position:absolute;left:120px;top:24px;width:20px;height:20px;border-radius:50%;background:var(--blue)}
.foot-links{position:absolute;left:160px;top:26px;display:flex}
.foot-links span{padding:0 10px;border-left:1px solid #555}
.foot-links span:first-child{border-left:none;padding-left:0}
.copyright{position:absolute;right:120px;top:26px}
</style>
</head>
<body>
<div class="page">
  <header class="site-header">
    <div class="brand"><span class="brand-mark"></span><span class="brand-name">TORVEL CAPITAL</span></div>
    <div class="util">LOG IN &nbsp;|&nbsp; ENG</div>
    <nav class="main-nav"><span>HOME</span><span>ABOUT</span><span>SERVICES</span><span>CURRENT ENGAGEMENTS</span><span>COMPLETED TRANSACTIONS</span></nav>
  </header>

  <section class="hero" role="img" aria-label="City skyline at sunset with high-rise towers">
    <h1 class="hero-title">A <small>BANK of</small> INVESTMENT</h1>
    <p class="hero-sub">One of the Leading Dallas-based Private Investment<br>Banking Advisory Firm!</p>
  </section>
  <div class="cta">Request Information
    <svg width="22" height="22" viewBox="0 0 22 22"><circle cx="11" cy="11" r="10" fill="#fff"/><path d="M9 6l5 5-5 5" stroke="#2a97c4" stroke-width="2.5" fill="none"/></svg>
  </div>

  <p class="intro"><b>T</b>orvel Capital is an independent investment bank working for buyers in a number of industries. We utilize exceptional technology in finding companies to meet our client's search criteria. We will not waste a buyer's time.</p>
  <div class="rule"></div>

  <section class="services">
    <div class="service">
      <svg viewBox="0 0 60 60" width="60"><path d="M8 50h44" stroke="#1c2a3a" stroke-width="3"/><path d="M12 44l14-14 8 8 16-20" stroke="#1c2a3a" stroke-width="4" fill="none"/><path d="M42 16h10v10" stroke="#2a97c4" stroke-width="4" fill="none"/></svg>
      <h3>Strategic Advisory</h3>
      <p>Lorem Ipsum is simply dummy text of the printing and typesetting industry. Lorem Ipsum has been the industry's</p>
      <a>Read More</a>
    </div>
    <div class="service">
      <svg viewBox="0 0 60 60" width="60"><path d="M14 12a24 24 0 0 0 0 36M46 12a24 24 0 0 1 0 36" stroke="#1c2a3a" stroke-width="4" fill="none"/><text x="30" y="40" text-anchor="middle" font-family="Open Sans, sans-serif" font-weight="700" font-size="28" fill="#2a97c4">$</text></svg>
      <h3>Current Engagements</h3>
      <p>Lorem Ipsum is simply dummy text of the printing and typesetting industry. Lorem Ipsum has been the industry's</p>
      <a>Read More</a>
    </div>
    <div class="service">
      <svg viewBox="0 0 60 60" width="60"><rect x="8" y="12" width="44" height="40" fill="none" stroke="#1c2a3a" stroke-width="4"/><rect x="8" y="12" width="44" height="9" fill="#1c2a3a"/><path d="M18 36l8 8 18-20" stroke="#2a97c4" stroke-width="5" fill="none"/></svg>
      <h3>Completed Transactions</h3>
      <p>Lorem Ipsum is simply dummy text of the printing and typesetting industry. Lorem Ipsum has been the industry's</p>
      <a>Read More</a>
    </div>
    <div class="service">
      <svg viewBox="0 0 60 60" width="60"><g stroke="#1c2a3a" stroke-width="3"><path d="M16 8v44M30 8v44M44 8v44"/></g><g fill="#2a97c4"><rect x="10" y="32" width="12" height="8"/><rect x="24" y="16" width="12" height="8"/><rect x="38" y="38" width="12" height="8"/></g></svg>
      <h3>Regulatory Compliance</h3>
      <p>Lorem Ipsum is simply dummy text of the printing and typesetting industry. Lorem Ipsum has been the industry's</p>
      <a>Read More</a>
    </div>
  </section>

  <section class="testimonials">
    <h2>Testimonials</h2>
    <div class="quotes">
      <div class="quote"><p>Integer vehicula velit quis erat ornare accu. Sed sed neque metus. Nullam mauris metus Integer vehicula velit quis erat ornare iaculis. Sed sed neque metus.</p><div class="avatar" role="img" aria-label="Client portrait"></div><div class="who">Marla Quinn<br>Lakemont Ohio</div></div>
      <div class="quote"><p>Integer vehicula velit quis erat ornare accu. Sed sed neque metus. Nullam mauris metus Integer vehicula velit quis erat ornare iaculis. Sed sed neque metus.</p><div class="avatar" role="img" aria-label="Client portrait"></div><div class="who">Marla Quinn<br>Lakemont Ohio</div></div>
      <div class="quote"><p>Integer vehicula velit quis erat ornare accu. Sed sed neque metus. Nullam mauris metus Integer vehicula velit quis erat ornare iaculis. Sed sed neque metus.</p><div class="avatar" role="img" aria-label="Client portrait"></div><div class="who">Marla Quinn<br>Lakemont Ohio</div></div>
    </div>
  </section>

  <section class="news">
    <h2>Latest News</h2>
    <div class="news-list">
      <article class="news-item"><h3>Lorem Ipsum Dolor Sit amet and typesetting</h3><p>Lorem Ipsum is simply dummy text of the printing and typesetting industry. Lorem Ipsum has been the industry Lorem Ipsum is simply dummy text of the printing and typesetting</p><time>01/27/16</time></article>
      <article class="news-item"><h3>Lorem Ipsum Dolor Sit amet and typesetting</h3><p>Lorem Ipsum is simply dummy text of the printing and typesetting industry. Lorem Ipsum has been the industry Lorem Ipsum is simply dummy text of the printing and typesetting</p><time>01/27/16</time></article>
      <article class="news-item"><h3>Lorem Ipsum Dolor Sit amet and typesetting</h3><p>Lorem Ipsum is simply dummy text of the printing and typesetting industry. Lorem Ipsum has been the industry Lorem Ipsum is simply dummy text of the printing and typesetting</p><time>01/27/16</time></article>
    </div>
  </section>
  <div class="more">More Press Releases</div>

  <footer class="site-footer">
    <span class="foot-brand"></span>
    <div class="foot-links"><span>Home</span><span>Terms &amp; Conditions</span><span>Contact Us</span></div>
    <div class="copyright">© 2016 Torvel Capital. All Rights Reserved</div>
  </footer>
</div>
</body>
</html>
```